Nivel Crest - Powerpoint Templates

We are a consultancy to help builders to optimize their planning in order to save building costs. For that reason we need templates for teasers and presentations where we offer our services, show our team and their capacities and present workflows, organization charts, price lists etc.

```html
<!DOCTYPE html>
<html lang="en">
<head>
<meta charset="utf-8">
<title>Nivel Crest – Presentation Templates</title>
<link href="https://fonts.googleapis.com/css2?family=Bebas+Neue&family=Montserrat:wght@400;500;600;700&display=swap" rel="stylesheet">
<style>
:root{
  --bg:#d9d9d9;
  --gold:#bd8530;
  --gold-light:#e4b75c;
  --gold-dark:#a86e22;
  --dark:#2e2f34;
  --dark-mid:#4b4c51;
  --steel:#8d8e92;
  --ink:#1d1d1f;
  --text:#333;
  --white:#fff;
  --sans:'Montserrat',Arial,sans-serif;
  --display:'Bebas Neue','Oswald',Impact,sans-serif;
}
*{box-sizing:border-box;margin:0;padding:0}
html,body{width:1200px;height:815px;overflow:hidden}
body{background:var(--bg);font-family:var(--sans);color:var(--text);position:relative}
.defs{position:absolute;width:0;height:0}
.slide{position:absolute;width:304px;height:190px;background:var(--white);overflow:hidden;box-shadow:0 9px 7px -5px rgba(0,0,0,.35)}
.slide>svg.bgshape{position:absolute;left:0;top:0;width:304px;height:190px}
.abs{position:absolute}
.col1{left:86px}.col2{left:448px}.col3{left:810px}
.row1{top:62px}.row2{top:305px}.row3{top:548px}

.heading{font-weight:700;font-size:13.5px;line-height:13px;color:var(--ink);letter-spacing:.2px}
.heading .accent{color:var(--gold)}
.heading.light,.heading.light .accent{color:var(--white)}
.center-title{left:0;right:0;text-align:center;font-weight:700;font-size:14px;color:var(--gold);letter-spacing:.4px}
.center-title.on-gold{color:var(--white)}
.intro{left:40px;right:40px;text-align:center;font-size:3.3px;line-height:5.5px;color:var(--text)}
.intro.on-gold{color:var(--white)}
.body{font-size:3.3px;line-height:5.3px;text-align:justify;color:var(--text)}
.body.on-dark{color:#eee}
.item-title{font-size:5px;font-weight:600;color:var(--ink)}
.item-title.gold{color:var(--gold-dark)}
.item-title.white{color:var(--white)}

.brand{display:flex;align-items:center;gap:4px;color:var(--white);font-weight:700;font-size:9px;letter-spacing:.6px}
.brand .mark{width:9px;height:9px;border:1.2px solid var(--white)}
.big-word{font-family:var(--display);color:var(--white);font-size:40px;line-height:36px;letter-spacing:.5px}
.pres{color:var(--white);font-weight:600;font-size:10.5px;line-height:10px}
.pres small{display:block;font-size:5.5px;line-height:7px;font-weight:600}
.prepared{color:var(--white);font-size:6.5px;line-height:7px;text-align:right;font-weight:500}

.member{width:62px;text-align:center}
.member .name{font-size:5.5px;font-weight:600;color:var(--ink);margin-bottom:1px}
.member .body{text-align:center;font-size:3.1px;line-height:3.9px}

.price-card{width:79px;height:97px;border:1px solid var(--gold);background:var(--white)}
.price-card .head{background:var(--gold);height:25px;text-align:center;color:var(--white)}
.price-card .label{font-size:5px;padding-top:2px;font-weight:500}
.price-card .amount{font-size:11px;line-height:12px}
.price-card .body{text-align:center;padding:11px 9px 0;font-size:3.1px;line-height:4px}
.price-card .total{position:absolute;left:18px;right:18px;bottom:6px;background:var(--gold);color:var(--white);font-size:3px;text-align:center;line-height:5px;font-weight:600}

.step{display:flex;align-items:center;gap:8px;width:62px}
.step .body{font-size:2.8px;line-height:3.4px;text-align:left}
</style>
</head>
<body>

<svg class="defs" aria-hidden="true">
  <defs>
    <linearGradient id="goldGrad" x1="0" y1="0" x2="1" y2="0">
      <stop offset="0" stop-color="#b87a28"/>
      <stop offset=".55" stop-color="#e3b65b"/>
      <stop offset="1" stop-color="#bd8430"/>
    </linearGradient>
    <linearGradient id="goldGradV" x1="0" y1="0" x2="1" y2="1">
      <stop offset="0" stop-color="#c48b35"/>
      <stop offset=".5" stop-color="#e2b45a"/>
      <stop offset="1" stop-color="#b0762a"/>
    </linearGradient>
    <linearGradient id="darkGrad" x1="0" y1="0" x2="1" y2="1">
      <stop offset="0" stop-color="#2c2d32"/>
      <stop offset=".6" stop-color="#46474c"/>
      <stop offset=".8" stop-color="#8e8f93"/>
      <stop offset="1" stop-color="#3a3b40"/>
    </linearGradient>
    <linearGradient id="steelGrad" x1="0" y1="0" x2="1" y2="0">
      <stop offset="0" stop-color="#2f3035"/>
      <stop offset=".5" stop-color="#6c6d72"/>
      <stop offset="1" stop-color="#2f3035"/>
    </linearGradient>
    <linearGradient id="cityGrad" x1="0" y1="0" x2="0" y2="1">
      <stop offset="0" stop-color="#3b4452"/>
      <stop offset=".5" stop-color="#6a7380"/>
      <stop offset="1" stop-color="#23272d"/>
    </linearGradient>
    <linearGradient id="skyGrad" x1="0" y1="0" x2="0" y2="1">
      <stop offset="0" stop-color="#8fb3d6"/>
      <stop offset=".55" stop-color="#c6d6e4"/>
      <stop offset="1" stop-color="#3e4f63"/>
    </linearGradient>
  </defs>
</svg>

<!-- Cover -->
<section class="slide col1 row1">
  <svg class="bgshape" viewBox="0 0 304 190">
    <g role="img" aria-label="City skyline photograph at dusk">
      <polygon points="124,0 304,0 304,190 224,190" fill="url(#cityGrad)"/>
    </g>
    <polygon points="0,0 124,0 224,190 0,190" fill="url(#goldGrad)"/>
    <polygon points="129,0 133,0 236,190 232,190" fill="var(--gold-light)"/>
    <polygon points="175,141 304,141 304,171 190,171" fill="url(#steelGrad)"/>
  </svg>
  <div class="abs brand" style="left:15px;top:12px"><span class="mark"></span>Nivel Crest</div>
  <div class="abs big-word" style="left:15px;top:64px">BUSINESS<br>SLIDES</div>
  <div class="abs prepared" style="right:30px;top:147px">PREPARED BY:<br>NAME GOES HERE</div>
  <div class="abs pres" style="left:15px;top:161px">PRESENTATION<small>TITLE GOESHERE</small></div>
</section>

<!-- About -->
<section class="slide col2 row1">
  <svg class="bgshape" viewBox="0 0 304 190">
    <polygon points="171,0 304,0 304,57 141,57" fill="url(#goldGrad)"/>
  </svg>
  <div class="abs body on-dark" style="left:166px;top:18px;width:128px;color:#fff">We help builders plan smarter, cut waste and protect budgets from the first sketch to handover.</div>
  <div class="abs heading" style="left:20px;top:30px">ABOUT<br><span class="accent">COMPANY</span></div>
  <div class="abs body" style="left:20px;top:73px;width:127px">Our consultants review drawings, schedules and tenders to find costly gaps before work starts on site.</div>
  <div class="abs body" style="left:159px;top:73px;width:127px">Our consultants review drawings, schedules and tenders to find costly gaps before work starts on site.</div>
  <div class="abs body" style="left:20px;top:110px;width:127px">We compare offers, check quantities and align trades so every phase runs on time. Clear reports show where money goes and which choices save the most across the whole project.</div>
  <div class="abs body" style="left:159px;top:110px;width:127px">We compare offers, check quantities and align trades so every phase runs on time. Clear reports show where money goes and which choices save the most across the whole project.</div>
</section>

<!-- Mission / Vision -->
<section class="slide col3 row1">
  <svg class="bgshape" viewBox="0 0 304 190">
    <rect x="165" y="32" width="139" height="56" fill="url(#goldGrad)"/>
    <rect x="165" y="102" width="139" height="56" fill="url(#steelGrad)"/>
    <polygon points="149,44 160,44 166,60 160,76 149,76 143,60" fill="url(#steelGrad)" stroke="#fff" stroke-width="1"/>
    <g fill="none" stroke="#fff" stroke-width="1"><circle cx="154.5" cy="58" r="4"/><line x1="152.5" y1="64" x2="156.5" y2="64"/></g>
    <polygon points="149,114 160,114 166,130 160,146 149,146 143,130" fill="url(#goldGradV)" stroke="#fff" stroke-width="1"/>
    <path d="M148 131 l4 -4 l3 2 l3 -2 l4 4 l-4 3 l-3 -2 l-3 2z" fill="#fff"/>
  </svg>
  <div class="abs heading" style="left:14px;top:30px">OUR MISSION<br><span class="accent">OUR VISION</span></div>
  <div class="abs body" style="left:14px;top:66px;width:127px">Our consultants review drawings, schedules and tenders to find costly gaps before work starts on site.</div>
  <div class="abs body" style="left:14px;top:110px;width:127px">We compare offers, check quantities and align trades so every phase runs on time. Clear reports show where money goes and which choices save the most across the whole project.</div>
  <div class="abs" style="left:189px;top:43px;width:103px"><div class="item-title white">Title Goes Here</div><div class="body" style="color:#fff">Lower building costs through careful planning, honest advice and clear numbers for every client we serve.</div></div>
  <div class="abs" style="left:189px;top:113px;width:103px"><div class="item-title white">Title Goes Here</div><div class="body" style="color:#fff">Lower building costs through careful planning, honest advice and clear numbers for every client we serve.</div></div>
</section>

<!-- Services -->
<section class="slide col1 row2">
  <svg class="bgshape" viewBox="0 0 304 190">
    <polygon points="180,0 304,0 304,190 77,190" fill="url(#darkGrad)"/>
    <g fill="none" stroke="#fff" stroke-width="1.2">
      <circle cx="195" cy="55" r="5" stroke-dasharray="2 1.2" stroke-width="2.2"/>
      <circle cx="195" cy="55" r="2"/>
      <circle cx="255" cy="55" r="6"/><ellipse cx="255" cy="55" rx="2.5" ry="6"/><line x1="249" y1="55" x2="261" y2="55"/>
      <path d="M195 112 v-8 M195 106 q-4 -1 -4 -5 q4 0 4 5 M195 104 q4 -1 4 -5 q-4 0 -4 5"/>
      <path d="M247 104 l4 -4 l4 2 l4 -2 l4 4 l-4 4 l-4 -3 l-4 3z"/>
    </g>
    <rect x="191" y="112" width="8" height="6" fill="#fff"/>
  </svg>
  <div class="abs heading" style="left:14px;top:25px">OUR COMPANY<br><span class="accent">SERVICES</span></div>
  <div class="abs" style="left:14px;top:62px;width:91px"><div class="item-title">Title Goes Here</div><div class="body">Cost checks for plans, tenders and contracts so builders know the real price before they commit.</div></div>
  <div class="abs" style="left:14px;top:96px;width:91px"><div class="item-title">Title Goes Here</div><div class="body">Cost checks for plans, tenders and contracts so builders know the real price before they commit.</div></div>
  <div class="abs body on-dark" style="left:171px;top:69px;width:48px">Clear advice on planning steps that keeps the build lean.</div>
  <div class="abs body on-dark" style="left:231px;top:69px;width:48px">Clear advice on planning steps that keeps the build lean.</div>
  <div class="abs body on-dark" style="left:171px;top:120px;width:48px">Clear advice on planning steps that keeps the build lean.</div>
  <div class="abs body on-dark" style="left:231px;top:120px;width:48px">Clear advice on planning steps that keeps the build lean.</div>
</section>

<!-- Creative team -->
<section class="slide col2 row2">
  <svg class="bgshape" viewBox="0 0 304 190">
    <rect x="0" y="0" width="304" height="96" fill="url(#goldGrad)"/>
    <g stroke="#fff" stroke-width="2" fill="url(#goldGradV)">
      <circle cx="52" cy="96" r="30"/><circle cx="118" cy="96" r="30"/><circle cx="184" cy="96" r="30"/><circle cx="250" cy="96" r="30"/>
    </g>
    <g fill="#fff">
      <circle cx="52" cy="91" r="4"/><path d="M45 103 q7 -9 14 0z"/>
      <circle cx="118" cy="91" r="4"/><path d="M111 103 q7 -9 14 0z"/>
      <circle cx="184" cy="91" r="4"/><path d="M177 103 q7 -9 14 0z"/>
      <circle cx="250" cy="91" r="4"/><path d="M243 103 q7 -9 14 0z"/>
    </g>
  </svg>
  <div class="abs center-title on-gold" style="top:22px">OUR CREATIVE TEAM</div>
  <div class="abs intro on-gold" style="top:41px">Meet the planners, estimators and site experts who turn complex builds into clear, affordable projects.</div>
  <div class="abs member" style="left:21px;top:131px"><div class="name">Name Here</div><div class="body">Planning expert with years of site work, focused on cost control and smooth schedules.</div></div>
  <div class="abs member" style="left:87px;top:131px"><div class="name">Name Here</div><div class="body">Planning expert with years of site work, focused on cost control and smooth schedules.</div></div>
  <div class="abs member" style="left:153px;top:131px"><div class="name">Name Here</div><div class="body">Planning expert with years of site work, focused on cost control and smooth schedules.</div></div>
  <div class="abs member" style="left:219px;top:131px"><div class="name">Name Here</div><div class="body">Planning expert with years of site work, focused on cost control and smooth schedules.</div></div>
</section>

<!-- Projects -->
<section class="slide col3 row2">
  <svg class="bgshape" viewBox="0 0 304 190">
    <polygon points="0,0 200,0 96,190 0,190" fill="url(#goldGradV)"/>
    <g stroke="#fff" stroke-width="1.2" fill="url(#goldGradV)">
      <polygon points="175,31 186,31 192,45 186,59 175,59 169,45"/>
      <polygon points="157,67 168,67 174,81 168,95 157,95 151,81"/>
      <polygon points="139,104 150,104 156,118 150,132 139,132 133,118"/>
      <polygon points="120,140 131,140 137,154 131,168 120,168 114,154"/>
    </g>
    <g fill="none" stroke="#fff" stroke-width=".9">
      <circle cx="180.5" cy="44" r="3.5"/><line x1="179" y1="49" x2="182" y2="49"/>
      <circle cx="162.5" cy="80" r="3.5"/><line x1="161" y1="85" x2="164" y2="85"/>
      <circle cx="144.5" cy="117" r="3.5"/><line x1="143" y1="122" x2="146" y2="122"/>
      <circle cx="125.5" cy="153" r="3.5"/><line x1="124" y1="158" x2="127" y2="158"/>
    </g>
  </svg>
  <div class="abs heading light" style="left:14px;top:25px">COMPANY<br>PROJECTS</div>
  <div class="abs body" style="left:14px;top:60px;width:110px;color:#fff">Our consultants review drawings, schedules and tenders to find costly gaps before work starts on site.</div>
  <div class="abs body" style="left:14px;top:96px;width:100px;color:#fff">Each project is tracked with simple reports so owners see progress, risks and savings at a glance.</div>
  <div class="abs" style="left:196px;top:30px;width:102px"><div class="item-title gold">Title Goes Here</div><div class="body">Short note on the project, the scope and the savings reached for the owner.</div></div>
  <div class="abs" style="left:178px;top:66px;width:102px"><div class="item-title gold">Title Goes Here</div><div class="body">Short note on the project, the scope and the savings reached for the owner.</div></div>
  <div class="abs" style="left:159px;top:103px;width:102px"><div class="item-title gold">Title Goes Here</div><div class="body">Short note on the project, the scope and the savings reached for the owner.</div></div>
  <div class="abs" style="left:141px;top:138px;width:102px"><div class="item-title gold">Title Goes Here</div><div class="body">Short note on the project, the scope and the savings reached for the owner.</div></div>
</section>

<!-- Pricing -->
<section class="slide col1 row3">
  <div class="abs center-title" style="top:20px">OUR CREATIVE TEAM</div>
  <div class="abs intro" style="top:40px">Simple packages for planning reviews, cost checks and full project support at fair fixed rates.</div>
  <div class="abs price-card" style="left:22px;top:71px"><div class="head"><div class="label">PRICE</div><div class="amount">$330</div></div><div class="body">Full plan review with cost report, tender check and one meeting to discuss the savings found.</div><div class="total">TOTAL $330</div></div>
  <div class="abs price-card" style="left:112px;top:71px"><div class="head"><div class="label">PRICE</div><div class="amount">$330</div></div><div class="body">Full plan review with cost report, tender check and one meeting to discuss the savings found.</div><div class="total">TOTAL $330</div></div>
  <div class="abs price-card" style="left:202px;top:71px"><div class="head"><div class="label">PRICE</div><div class="amount">$330</div></div><div class="body">Full plan review with cost report, tender check and one meeting to discuss the savings found.</div><div class="total">TOTAL $330</div></div>
</section>

<!-- Infographic -->
<section class="slide col2 row3">
  <svg class="bgshape" viewBox="0 0 304 190">
    <circle cx="152" cy="117" r="45" fill="url(#goldGradV)"/>
    <circle cx="152" cy="117" r="28" fill="url(#darkGrad)" stroke="#fff" stroke-width="1.5"/>
    <g fill="#fff">
      <circle cx="146" cy="111" r="3.2"/><path d="M139 124 q7 -10 14 0z"/>
      <circle cx="158" cy="111" r="3.2"/><path d="M151 124 q7 -10 14 0z"/>
      <circle cx="152" cy="109" r="3.8"/><path d="M144 126 q8 -12 16 0z"/>
    </g>
    <g fill="#fff" font-family="Montserrat,sans-serif" font-size="4.2" font-weight="600" text-anchor="middle">
      <text x="152" y="79">50%</text><text x="152" y="159">50%</text>
      <text x="128" y="91" transform="rotate(-45 128 91)">50%</text>
      <text x="176" y="91" transform="rotate(45 176 91)">50%</text>
      <text x="116" y="119" transform="rotate(-90 116 119)">50%</text>
      <text x="188" y="119" transform="rotate(90 188 119)">50%</text>
      <text x="128" y="145" transform="rotate(45 128 145)">50%</text>
      <text x="176" y="145" transform="rotate(-45 176 145)">50%</text>
    </g>
    <g fill="none" stroke="var(--gold)" stroke-width="1">
      <path d="M42 92 l4 -4 l3 2 l3 -2 l4 4 l-4 3 l-3 -2 l-3 2z"/>
      <rect x="45" y="116" width="8" height="5.5"/><line x1="46" y1="124" x2="52" y2="124"/>
      <path d="M49 152 v-6 M49 148 q-3 -1 -3 -4 q3 0 3 4 M49 147 q3 -1 3 -4 q-3 0 -3 4"/>
      <circle cx="215" cy="90" r="3.5"/><line x1="213.5" y1="95" x2="216.5" y2="95"/>
      <circle cx="215" cy="118" r="4"/><ellipse cx="215" cy="118" rx="1.6" ry="4"/><line x1="211" y1="118" x2="219" y2="118"/>
      <circle cx="215" cy="147" r="3.5" stroke-dasharray="1.6 1" stroke-width="1.8"/>
    </g>
    <rect x="46" y="152" width="6" height="4" fill="var(--gold)"/>
  </svg>
  <div class="abs center-title" style="top:20px">INFOGRAPHIC CHART</div>
  <div class="abs intro" style="top:40px">Our workflow splits every build into clear stages, each checked for cost, time and quality.</div>
  <div class="abs step" style="left:59px;top:85px"><div class="body">Short note on this step of the workflow.</div></div>
  <div class="abs step" style="left:59px;top:113px"><div class="body">Short note on this step of the workflow.</div></div>
  <div class="abs step" style="left:59px;top:143px"><div class="body">Short note on this step of the workflow.</div></div>
  <div class="abs step" style="left:224px;top:85px"><div class="body">Short note on this step of the workflow.</div></div>
  <div class="abs step" style="left:224px;top:113px"><div class="body">Short note on this step of the workflow.</div></div>
  <div class="abs step" style="left:224px;top:143px"><div class="body">Short note on this step of the workflow.</div></div>
</section>

<!-- Thank you -->
<section class="slide col3 row3">
  <svg class="bgshape" viewBox="0 0 304 190">
    <rect x="0" y="0" width="304" height="190" fill="url(#darkGrad)"/>
    <g role="img" aria-label="Photograph of a city skyline under a blue sky">
      <polygon points="130,0 304,0 304,190 235,190" fill="url(#skyGrad)"/>
    </g>
    <polygon points="128,0 132,0 236,190 232,190" fill="var(--gold-light)"/>
  </svg>
  <div class="abs brand" style="left:15px;top:12px"><span class="mark"></span>Nivel Crest</div>
  <div class="abs big-word" style="left:15px;top:64px">THANK<br>YOU!</div>
  <div class="abs pres" style="left:15px;top:161px">PRESENTATION<small>TITLE GOESHERE</small></div>
</section>

</body>
</html>
```